New Bicycle shop business card

Hi!
I'm looking for a business card for my new proffesional bike mechanics shop. This shop is only for fixing broken bikes and not selling bikes.
Peferbly a modern and sleek and modern design.
Colors: black, grey, red, white
Information:
Name: Rijwielwerkplaats Vanhoutte
Shop owner: Bart Vanhoutte & Marieke Segers
Website: www.rijwielwerkplaats-vanhoutte.be
Email: info@rijwielwerkplaats-vanhoutte.be
Phone number: +32471902368
Street adres: Kerkweg 46
9940 Bellebeke
Slogan/shop information: Herstellingen van alle merken.
Logo: see files.
Target Market(s)
People who seek a mechanic to fix or upgrade their bikes.
Contact Information for Business Card
Information:
Website: info@rijwielwerkplaats-vanhoutte.be
9940 Bellebeke
Logo: see files.

```html
<!DOCTYPE html>
<html lang="nl">
<head>
<meta charset="utf-8">
<title>Rijwielwerkplaats Vanhoutte – visitekaartje</title>
<link rel="stylesheet" href="https://fonts.googleapis.com/css2?family=Montserrat:wght@800&family=Roboto:wght@400;500&display=swap">
<style>
  :root {
    --backdrop: #3b3b3d;
    --card: #1d1d1f;
    --card-edge: #141415;
    --red: #e0283a;
    --white: #ffffff;
    --grey: #8e8e93;
    --grey-light: #c9c9cc;
  }
  * { margin: 0; padding: 0; box-sizing: border-box; }
  html, body {
    width: 799px; height: 1200px; overflow: hidden;
    background: var(--backdrop);
    font-family: "Roboto", Arial, sans-serif;
    color: var(--white);
  }
  .sheet {
    width: 799px; height: 1200px;
    display: flex; flex-direction: column; align-items: center; justify-content: center;
    gap: 120px;
  }
  .card {
    position: relative;
    width: 600px; height: 360px;
    background: var(--card);
    border-radius: 22px;
    overflow: hidden;
    box-shadow: 0 14px 30px rgba(0,0,0,.45);
  }

  /* wordmark */
  .brand { display: flex; flex-direction: column; align-items: center; text-align: center; }
  .brand-mark { width: 44px; height: 44px; background: var(--red); border-radius: 6px; margin-bottom: 16px; }
  .brand-name {
    font-family: "Montserrat", Arial, sans-serif; font-weight: 800;
    text-transform: uppercase; color: var(--white); line-height: 1.15;
    letter-spacing: 1px;
  }

  /* front */
  .card-front .brand { position: absolute; top: 82px; left: 0; right: 0; }
  .card-front .brand-name { font-size: 30px; }
  .card-front .site {
    position: absolute; left: 0; right: 0; top: 270px; text-align: center;
    font-size: 16px; color: var(--grey-light);
  }
  .site .accent { color: var(--red); }

  /* back */
  .card-back .brand { position: absolute; left: 20px; width: 270px; top: 64px; }
  .card-back .brand-mark { width: 36px; height: 36px; margin-bottom: 14px; }
  .card-back .brand-name { font-size: 19px; }
  .divider {
    position: absolute; left: 302px; top: 44px; width: 1px; height: 196px;
    background: var(--grey);
  }
  .contact { position: absolute; left: 322px; top: 48px; right: 16px; }
  .person {
    font-family: "Montserrat", Arial, sans-serif; font-weight: 800;
    font-size: 21px; color: var(--red); text-transform: uppercase; letter-spacing: .5px;
  }
  .role { font-size: 13px; color: var(--white); margin: 2px 0 16px; }
  .contact-list { list-style: none; font-size: 13px; }
  .contact-list li { display: flex; align-items: center; gap: 8px; height: 24px; white-space: nowrap; }
  .contact-list svg { width: 12px; height: 12px; flex: none; fill: var(--red); }
  .contact-list .address { padding-left: 0; margin-top: 2px; }

  .band-rule {
    position: absolute; left: 0; right: 0; top: 262px; height: 5px; background: var(--grey);
  }
  .band {
    position: absolute; left: 0; right: 0; top: 267px; bottom: 0; background: var(--red);
  }
  .slogan {
    position: absolute; left: 40px; top: 16px; font-size: 16px; color: var(--white);
  }
</style>
</head>
<body>
<main class="sheet">

  <section class="card card-front" aria-label="Voorzijde">
    <div class="brand">
      <span class="brand-mark"></span>
      <p class="brand-name">Rijwielwerkplaats<br>Vanhoutte</p>
    </div>
    <p class="site">www.rijwielwerkplaats-<span class="accent">vanhoutte</span>.be</p>
  </section>

  <section class="card card-back" aria-label="Achterzijde">
    <div class="brand">
      <span class="brand-mark"></span>
      <p class="brand-name">Rijwielwerkplaats<br>Vanhoutte</p>
    </div>
    <span class="divider"></span>
    <div class="contact">
      <p class="person">Marieke Segers</p>
      <p class="role">Owner</p>
      <ul class="contact-list">
        <li>
          <svg viewBox="0 0 24 24" aria-hidden="true"><path d="M6.6 10.8a15.1 15.1 0 0 0 6.6 6.6l2.2-2.2c.3-.3.7-.4 1-.2 1.1.4 2.3.6 3.6.6.6 0 1 .4 1 1V20c0 .6-.4 1-1 1A17 17 0 0 1 3 4c0-.6.4-1 1-1h3.5c.6 0 1 .4 1 1 0 1.3.2 2.5.6 3.6.1.3 0 .7-.2 1z"/></svg>
          +32471902368
        </li>
        <li>
          <svg viewBox="0 0 24 24" aria-hidden="true"><path d="M2 5h20v14H2z M3.5 6.5 12 13l8.5-6.5" stroke="#1d1d1f" stroke-width="1.6"/></svg>
          www.rijwielwerkplaats-vanhoutte.be
        </li>
        <li>
          <svg viewBox="0 0 24 24" aria-hidden="true"><circle cx="12" cy="12" r="10"/><path d="M2 12h20M12 2c3 3 3 17 0 20M12 2c-3 3-3 17 0 20" stroke="#1d1d1f" stroke-width="1.5" fill="none"/></svg>
          info@rijwielwerkplaats-vanhoutte.be
        </li>
        <li class="address">Kerkweg 46 9940 Bellebeke</li>
      </ul>
    </div>
    <span class="band-rule"></span>
    <div class="band">
      <p class="slogan">Herstellingen van alle merken</p>
    </div>
  </section>

</main>
</body>
</html>
```